New stationary design for online film company

We need some new stationary to fit with our new logo. The stationary should be professional, clean and simple.
We need designs for a full set of business stationary.
We need - letterhead, envelopes, invoices, proposals, coverslip/note and cover page

Industry/Entity Type

Business

```html
<!DOCTYPE html>
<html lang="en">
<head>
<meta charset="utf-8">
<title>Orbitreel Stationery Set</title>
<link href="https://fonts.googleapis.com/css2?family=Nunito:wght@400;600;800&display=swap" rel="stylesheet">
<style>
  :root {
    --navy: #0b4670;
    --sky: #6aa4c1;
    --paper: #ffffff;
    --ink: #333b44;
    --backdrop: #e6e3df;
    --faint: #e4ebef;
    --rule: #8a8a8a;
  }
  * { margin: 0; padding: 0; box-sizing: border-box; }
  html, body { width: 1200px; height: 757px; overflow: hidden; }
  body {
    position: relative;
    background: var(--backdrop);
    font-family: "Nunito", sans-serif;
    color: var(--ink);
  }
  .brand {
    display: flex; align-items: center; gap: 8px;
    font-family: "Nunito", sans-serif;
    font-weight: 800;
    color: var(--navy);
    letter-spacing: -0.3px;
    line-height: 1;
  }
  .brand-dot {
    border-radius: 50%;
    border: 3px solid var(--navy);
    display: inline-block;
    flex: none;
  }
  .band {
    height: 100%; background: var(--sky);
    display: flex; align-items: center; justify-content: center;
    font-size: 7.5px; font-weight: 600; letter-spacing: 2px; color: #10324a;
  }

  /* Letterhead */
  .letterhead {
    position: absolute; left: 15px; top: 19px; width: 508px; height: 717px;
    background: var(--paper);
    box-shadow: 0 2px 6px rgba(0,0,0,.18);
  }
  .letterhead .brand { position: absolute; left: 28px; top: 20px; font-size: 32px; }
  .letterhead .brand-dot { width: 30px; height: 30px; }
  .letterhead-contact {
    position: absolute; left: 415px; top: 18px;
    border-left: 1px solid #9aa3aa; padding-left: 6px;
    font-size: 5.6px; line-height: 1.4;
  }
  .letterhead-contact p { margin-bottom: 4px; }
  .letterhead-footer {
    position: absolute; left: 0; right: 0; top: 662px; height: 29px;
    border-top: 1px solid var(--navy); border-bottom: 1px solid var(--navy);
    padding: 3px 0;
  }

  /* Business cards */
  .card {
    position: absolute; width: 215px; height: 123px;
    box-shadow: 0 2px 5px rgba(0,0,0,.18);
  }
  .card-back { left: 576px; top: 13px; background: var(--sky); }
  .card-back .mark {
    position: absolute; left: 80px; top: 42px;
    width: 54px; height: 54px; border-radius: 50%;
    border: 6px solid var(--paper);
  }
  .card-back .url {
    position: absolute; bottom: 7px; width: 100%; text-align: center;
    font-size: 5.5px; letter-spacing: 1.6px; color: var(--paper);
  }
  .card-front { left: 800px; top: 14px; background: var(--paper); }
  .card-front .brand { position: absolute; left: 33px; top: 13px; font-size: 27px; gap: 6px; }
  .card-front .brand-dot { width: 25px; height: 25px; }
  .card-front .info {
    position: absolute; left: 0; right: 0; top: 61px; height: 48px;
    background: var(--sky);
    border-top: 1px solid var(--paper); outline: 1px solid var(--sky);
    display: flex; justify-content: center; gap: 6px;
    padding-top: 4px; font-size: 5.2px; color: var(--navy); line-height: 1.8;
  }
  .card-front .address {
    text-align: right; padding-right: 5px; border-right: 1px solid var(--paper);
    height: 26px; margin-top: 6px; line-height: 1.4;
  }
  .card-front .holder {
    position: absolute; bottom: 3px; width: 100%; text-align: center;
    font-size: 7.5px; font-weight: 800; color: var(--navy);
  }
  .card-front .holder span { font-weight: 400; color: var(--sky); font-size: 6px; }

  /* Envelopes */
  .envelopes { position: absolute; left: 0; top: 0; width: 1200px; height: 757px; pointer-events: none; }
  .envelope-front {
    position: absolute; left: 602px; top: 455px; width: 584px; height: 261px;
    background: var(--paper); border: 1px solid #b9b9b9;
  }
  .envelope-front .brand { position: absolute; left: 22px; top: 12px; font-size: 31px; }
  .envelope-front .brand-dot { width: 29px; height: 29px; }
  .envelope-front .address {
    position: absolute; left: 22px; top: 66px; font-size: 8.5px; letter-spacing: 0.8px;
  }
  .envelope-front .faint-mark {
    position: absolute; left: 510px; top: 135px; width: 54px; height: 54px;
    border-radius: 50%; border: 6px solid var(--faint);
  }
  .envelope-front .footer {
    position: absolute; left: 0; right: 0; top: 209px; height: 29px;
    border-top: 1px solid var(--sky); border-bottom: 1px solid var(--sky); padding: 2px 0;
  }
  .envelope-front .band { justify-content: flex-start; padding-left: 22px; }
</style>
</head>
<body>

<section class="letterhead">
  <div class="brand"><span class="brand-dot"></span>orbitreel</div>
  <div class="letterhead-contact">
    <p>&#9990; 123-456-7890</p>
    <p>&#9993; info@orbitreel.com</p>
    <p>00, Complex Name<br>street, city 000452</p>
  </div>
  <div class="letterhead-footer"><div class="band">www.orbitreel.com</div></div>
</section>

<section class="card card-back">
  <div class="mark"></div>
  <p class="url">www.orbitreel.com</p>
</section>

<section class="card card-front">
  <div class="brand"><span class="brand-dot"></span>orbitreel</div>
  <div class="info">
    <div class="address">00, Complex Name<br>street, city<br>000452</div>
    <div>&#9990; 123-456-7890<br>&#9743; 123-456-7890<br>&#9993; info@orbitreel.com<br>&#9673; www.orbitreel.com</div>
  </div>
  <p class="holder">Your Name, <span>Designation</span></p>
</section>

<svg class="envelopes" viewBox="0 0 1200 757" aria-hidden="true">
  <rect x="573" y="160" width="582" height="200" fill="var(--paper)"/>
  <path d="M573,160 H1155 L1146,195 Q1138,212 1118,216 L866,260 L612,216 Q592,212 584,195 Z" fill="var(--sky)"/>
  <circle cx="864" cy="204" r="19" fill="none" stroke="var(--paper)" stroke-width="5"/>
  <path d="M573,238 H1155 L1146,272 Q1138,288 1116,292 L878,338 Q866,341 854,338 L614,292 Q592,288 584,272 Z" fill="var(--navy)"/>
  <circle cx="864" cy="295" r="19" fill="none" stroke="var(--paper)" stroke-width="5"/>
  <rect x="560.5" y="351.5" width="584" height="261" fill="var(--paper)" stroke="var(--rule)"/>
  <path d="M561,352 Q566,395 600,405 L838,452 Q853,456 868,452 L1108,403 Q1134,396 1144,352" fill="none" stroke="#333"/>
  <circle cx="852" cy="410" r="18" fill="none" stroke="var(--navy)" stroke-width="5"/>
</svg>

<section class="envelope-front">
  <div class="brand"><span class="brand-dot"></span>orbitreel</div>
  <p class="address">00, Complex Name, street, city 000452</p>
  <div class="faint-mark"></div>
  <div class="footer"><div class="band">www.orbitreel.com</div></div>
</section>

</body>
</html>
```